Brevlon Website Design - Wordpress

Need a website WordPress design for our existing website that we just stood up. The logo is already in place and name. Brevlon.example We are a company which makes connections with our clients through educating them and providing networking events. We would like for the website to show a VIP/special feel to it.

Target Market(s)

Business executives and employees. Age group 26-65 in the following sectors:
- Technology
- Human Resources
- Finance
- Sales

Industry/Entity Type

Technical Service

Number of Pages Required

4 page

Font styles to use
Sans Serif

Requirements
Must have
• Must be something for Wordpress
Nice to have
• Would like this to be professional but look cutting edge and VIP.

```html
<!DOCTYPE html>
<html lang="en">
<head>
<meta charset="utf-8">
<title>Brevlon – Expand Your Business</title>
<link rel="stylesheet" href="https://fonts.googleapis.com/css2?family=Montserrat:wght@300;400;600;700&family=Open+Sans:wght@400;600&display=swap">
<style>
:root{
  --bg:#0b0b0d;
  --white:#ffffff;
  --muted:#b9b9bd;
  --blue:#1f7fc8;
  --red:#e1262d;
  --purple:#7d3a98;
  --yellow:#f2b41b;
  --green:#3aa64b;
  --line:rgba(255,255,255,.55);
}
*{margin:0;padding:0;box-sizing:border-box}
html,body{width:1200px;height:3584px;overflow:hidden;background:var(--bg)}
body{position:relative;font-family:"Open Sans",Arial,sans-serif;color:var(--white)}
h1,h2,h3,.brand,.nav,.btn{font-family:"Montserrat",Helvetica,sans-serif}
.abs{position:absolute}

/* header */
.site-header{left:0;top:0;width:1200px;height:140px;background:#000}
.brand{display:flex;align-items:center;gap:16px;font-weight:400;letter-spacing:6px;color:var(--white)}
.brand-mark{width:26px;height:26px;background:var(--white)}
.header-brand{left:110px;top:40px;font-size:44px}
.contact-top{top:18px;display:flex;gap:14px;align-items:center;font-size:14px;line-height:19px}
.contact-top .ico{width:36px;height:36px;border-radius:50%;background:#222;display:flex;align-items:center;justify-content:center}
.contact-top .lbl{color:var(--red);font-size:13px}
.nav{display:flex;gap:42px;font-size:15px;font-weight:600;letter-spacing:.5px}
.nav a{color:var(--white);text-decoration:none}
.nav a.active{color:var(--red)}
.header-nav{left:676px;top:98px}

/* hero */
.hero{left:0;top:140px;width:1200px;height:780px;background:radial-gradient(ellipse at 70% 40%,#2b2b2f 0%,#111114 60%,#08080a 100%)}
.hero-media{left:110px;top:40px;width:400px;height:700px;background:linear-gradient(180deg,#9fb3c8 0%,#4e6680 45%,#1c2530 100%)}
.hero-brand{left:560px;top:230px;width:600px;justify-content:center;font-size:78px;font-weight:300;letter-spacing:14px}
.hero-title{left:560px;top:345px;width:600px;text-align:center;font-size:40px;font-weight:700;letter-spacing:1px}

/* about */
.about-media{left:220px;top:1000px;width:300px;height:480px;background:linear-gradient(160deg,#3a4a66,#2a1e33 50%,#5a4a2a)}
.section-title{font-size:32px;font-weight:700;letter-spacing:1px}
.about-title{left:572px;top:1005px}
.body-text{font-size:14.5px;line-height:25px;color:var(--muted)}
.about-text{left:572px;top:1070px;width:560px}
.btn{display:inline-flex;align-items:center;gap:10px;background:var(--green);color:var(--white);font-size:14px;font-weight:700;padding:12px 22px;letter-spacing:.5px}
.about-btn{left:572px;top:1290px}

/* strategy */
.strategy{left:0;top:1580px;width:1200px;height:800px;background:radial-gradient(ellipse at 50% 55%,#2e2e31 0%,#121214 65%,var(--bg) 100%)}
.center{text-align:center}
.strategy-title{left:0;top:1645px;width:1200px}
.strategy-text{left:240px;top:1700px;width:720px;text-align:center}
.strategy-media{left:400px;top:1800px;width:400px;height:540px;background:linear-gradient(135deg,var(--blue) 0%,#3a2a4a 45%,var(--yellow) 100%);opacity:.85}
.pillar{width:300px}
.pillar h3{font-size:24px;font-weight:700;letter-spacing:1px;margin-bottom:10px}
.pillar.left{text-align:right}
.mind h3{color:var(--blue)}
.heart h3{color:var(--red)}
.soul h3{color:var(--purple)}
.strength h3{color:var(--yellow)}

/* offer */
.offer-title{left:0;top:2455px;width:1200px}
.offer-text{left:300px;top:2510px;width:600px;text-align:center}
.card{top:2600px;width:310px;height:250px;border:1px solid var(--line);padding:26px 28px;text-align:center;background:rgba(10,10,12,.6)}
.card h3{font-size:18px;font-weight:700;letter-spacing:1px;margin:14px 0 10px}
.card .body-text{font-size:13px;line-height:21px}
.card .more{margin-top:12px;font-size:13px;color:var(--green)}
.educate h3{color:var(--blue)}
.equip h3{color:var(--red)}
.exchange h3{color:var(--purple)}

/* footer */
.footer-brand{left:0;top:3020px;width:1200px;justify-content:center;font-size:96px;font-weight:300;letter-spacing:18px}
.footer-brand .brand-mark{width:40px;height:40px}
.f-contact{top:3280px;width:260px;text-align:center;font-size:15px;line-height:23px;font-weight:600}
.f-contact svg{display:block;margin:0 auto 14px}
.footer-nav{left:0;top:3495px;width:1200px;justify-content:center;gap:26px;font-size:14px}
.copyright{left:0;top:3540px;width:1200px;text-align:center;font-size:12px;color:var(--muted)}
</style>
</head>
<body>

<header class="site-header abs">
  <div class="brand header-brand abs"><span class="brand-mark"></span>BREVLON</div>
  <div class="contact-top abs" style="left:676px">
    <span class="ico"><svg width="18" height="18" viewBox="0 0 24 24" fill="#fff"><path d="M6.6 10.8a15.1 15.1 0 0 0 6.6 6.6l2.2-2.2c.3-.3.7-.4 1-.2 1.1.4 2.3.6 3.6.6.6 0 1 .4 1 1V20c0 .6-.4 1-1 1C10.6 21 3 13.4 3 4c0-.6.4-1 1-1h3.5c.6 0 1 .4 1 1 0 1.3.2 2.5.6 3.6.1.3 0 .7-.2 1z"/></svg></span>
    <div><div class="lbl">Support/call us</div>1-800 555 0142</div>
  </div>
  <div class="contact-top abs" style="left:940px">
    <span class="ico"><svg width="18" height="18" viewBox="0 0 24 24" fill="none" stroke="#fff" stroke-width="2"><rect x="3" y="5" width="18" height="14"/><path d="M3 6l9 7 9-7"/></svg></span>
    <div><div class="lbl">Email us</div>info@brevlon.example</div>
  </div>
  <nav class="nav header-nav abs"><a class="active">Home</a><a>Events</a><a>Expert</a><a>X</a><a>About</a><a>Connect</a></nav>
</header>

<section class="hero abs">
  <div class="hero-media abs" role="img" aria-label="Photo of a businessman standing in a bright keyhole-shaped doorway opening onto the sky"></div>
  <div class="brand hero-brand abs">BREVLON</div>
  <h1 class="hero-title abs">EXPAND YOUR BUSINESS</h1>
  <svg class="abs" style="left:0;top:690px" width="1200" height="90"><polygon points="0,40 580,70 0,90" fill="var(--blue)"/><polygon points="0,60 220,80 0,90" fill="var(--red)"/></svg>
</section>

<section>
  <div class="about-media abs" role="img" aria-label="Large four-colour X shape filled with city and people photography"></div>
  <h2 class="section-title about-title abs">ABOUT US</h2>
  <p class="body-text about-text abs">We build lasting connections between professionals through focused education and curated networking events. Our members gain access to leaders, ideas and opportunities that move careers and companies forward. Every gathering is designed with care, giving executives and teams a private space to learn, share and grow together, with guidance from experienced mentors across technology, finance and sales.</p>
  <a class="btn about-btn abs">READ MORE <svg width="14" height="14" viewBox="0 0 24 24"><circle cx="12" cy="12" r="11" fill="#fff"/><path d="M10 7l5 5-5 5" stroke="var(--green)" stroke-width="3" fill="none"/></svg></a>
</section>

<section class="strategy abs"></section>
<svg class="abs" style="left:0;top:1500px" width="1200" height="90"><polygon points="740,45 1200,0 1200,90" fill="var(--yellow)"/></svg>
<h2 class="section-title strategy-title center abs">OUR UNIQUE X STRATEGY</h2>
<p class="body-text strategy-text abs">Brevlon is powerfully effective because our approach is "Humanistic". Our materials are founded upon the idea that Culture is a Person. Our founder developed this philosophy on culture over more than three decades, learning from leaders and communities around the globe.</p>
<div class="strategy-media abs" role="img" aria-label="Silhouette of a person standing before a large four-colour X"></div>
<div class="pillar left mind abs" style="left:80px;top:1830px"><h3>MIND</h3><p class="body-text">Sharpen strategic thinking with practical lessons drawn from leaders who have built great teams.</p></div>
<div class="pillar heart abs" style="left:830px;top:1830px"><h3>HEART</h3><p class="body-text">Lead with empathy and purpose so people feel valued, heard and ready to give their best.</p></div>
<div class="pillar left soul abs" style="left:80px;top:2080px"><h3>SOUL</h3><p class="body-text">Shape a culture with meaning, where shared values guide each choice your company makes.</p></div>
<div class="pillar strength abs" style="left:830px;top:2080px"><h3>STRENGTH</h3><p class="body-text">Turn insight into action with tools that build resilient teams and steady long-term growth.</p></div>
<svg class="abs" style="left:0;top:2250px" width="1200" height="90"><polygon points="0,10 600,80 0,90" fill="var(--purple)"/></svg>

<h2 class="section-title offer-title center abs">WHAT WE OFFER YOU</h2>
<p class="body-text offer-text abs">Programs, resources and a trusted network built for ambitious professionals who want to lead with clarity and grow their reach.</p>
<svg class="abs" style="left:36px;top:2705px" width="30" height="30" viewBox="0 0 24 24"><path d="M15 4l-8 8 8 8" stroke="var(--green)" stroke-width="2.5" fill="none"/></svg>
<svg class="abs" style="left:1134px;top:2705px" width="30" height="30" viewBox="0 0 24 24"><path d="M9 4l8 8-8 8" stroke="var(--green)" stroke-width="2.5" fill="none"/></svg>
<div class="card educate abs" style="left:90px">
  <svg width="40" height="34" viewBox="0 0 24 20"><path d="M1 2h8c2 0 3 1 3 2v15c0-1-1-2-3-2H1zM23 2h-8c-2 0-3 1-3 2v15c0-1 1-2 3-2h8z" fill="var(--blue)"/></svg>
  <h3>EDUCATE</h3><p class="body-text">At Brevlon we provide effective training and learning as the foundation for building a healthy, successful company.</p><p class="more">Read more ›</p>
</div>
<div class="card equip abs" style="left:445px">
  <svg width="40" height="34" viewBox="0 0 24 20"><rect x="2" y="6" width="20" height="12" rx="1" fill="var(--red)"/><path d="M8 6V3h8v3" stroke="var(--red)" stroke-width="2" fill="none"/></svg>
  <h3>EQUIP</h3><p class="body-text">Through our expert network of companies, we'll help find the right partner for the resources you need to move.</p><p class="more">Read more ›</p>
</div>
<div class="card exchange abs" style="left:800px">
  <svg width="40" height="34" viewBox="0 0 24 20"><path d="M3 6h16l-4-4M21 14H5l4 4" stroke="var(--purple)" stroke-width="2.5" fill="none"/></svg>
  <h3>EXCHANGE</h3><p class="body-text">We connect you with others who have successfully implemented our X Strategy to facilitate growth in their business.</p><p class="more">Read more ›</p>
</div>
<svg class="abs" style="left:0;top:2930px" width="1200" height="90"><polygon points="520,60 1200,0 1200,90" fill="var(--red)"/></svg>

<footer>
  <div class="brand footer-brand abs"><span class="brand-mark"></span>BREVLON</div>
  <div class="f-contact abs" style="left:160px">
    <svg width="56" height="56" viewBox="0 0 56 56" fill="none" stroke="#fff" stroke-width="2"><path d="M2 14V2h12M42 2h12v12M54 42v12H42M14 54H2V42"/><path d="M28 14a9 9 0 0 1 9 9c0 7-9 17-9 17s-9-10-9-17a9 9 0 0 1 9-9z"/><circle cx="28" cy="23" r="3"/></svg>
    2190 Harbor Lane<br>Fairview, MT 59000
  </div>
  <div class="f-contact abs" style="left:470px">
    <svg width="56" height="56" viewBox="0 0 56 56" fill="none" stroke="#fff" stroke-width="2"><path d="M2 14V2h12M42 2h12v12M54 42v12H42M14 54H2V42"/><path d="M20 16h5l2 6-3 2a14 14 0 0 0 6 6l2-3 6 2v5c0 1-1 2-2 2-11 0-18-7-18-18 0-1 1-2 2-2z"/></svg>
    Phone<br>1-800 555 0142
  </div>
  <div class="f-contact abs" style="left:780px">
    <svg width="56" height="56" viewBox="0 0 56 56" fill="none" stroke="#fff" stroke-width="2"><path d="M2 14V2h12M42 2h12v12M54 42v12H42M14 54H2V42"/><rect x="15" y="19" width="26" height="18"/><path d="M15 20l13 9 13-9"/></svg>
    Email<br>info@brevlon.example
  </div>
  <nav class="nav footer-nav abs"><a>HOME</a><a>•</a><a>EVENTS</a><a>•</a><a>EXPERT</a><a>•</a><a>X</a><a>•</a><a>ABOUT</a><a>•</a><a>CONNECT</a></nav>
  <p class="copyright abs">Copyright © 2016. All rights reserved.</p>
</footer>

</body>
</html>
```